Professional BIO Template with photo and logo

Hello,
I need a professional Bio template developed via Microsoft WORD ASAP!!!!! I would like to just be able to add the text I need to add. So resize-able text boxes. Potentially able to adjust the font. These are the things I need added it to include.
Head shot (attached)
Text Box for Name
Text Box for phone number
Text box for email
KVT Logo (attached)
Maybe a blue banner at the top or some background boxes that are blue or grey. Here are the pantone colors that our company uses.

CORE COLOR
100c 91m 17y 6k 38r 58g 128b Hex #263A80 Pantone 7687 C

CORE CONTRAST COLOR
36c 29m 28y 0k 168r 168g 170b Hex #669999 Pantone Cool Gray 6C

I also attached some examples of what we have been looking at. Instead of green add the blue...instead of black maybe just be white.

Thank you

```html
<!DOCTYPE html>
<html lang="en">
<head>
<meta charset="utf-8">
<title>Bio Sheet – Daniel Morrow</title>
<link href="https://fonts.googleapis.com/css2?family=Arimo:wght@400;700&family=Tinos:ital@1&family=Roboto+Condensed:wght@400&display=swap" rel="stylesheet">
<style>
  :root {
    --core-blue: #263a80;
    --band-blue: #2f47a0;
    --title-blue: #2f3a8a;
    --contrast-gray: #a8a8aa;
    --light-gray: #e4e4e6;
    --page-bg: #d9d9d9;
    --ink: #2b2b2b;
    --white: #ffffff;
  }
  * { box-sizing: border-box; margin: 0; padding: 0; }
  html, body { width: 1200px; height: 1113px; overflow: hidden; background: var(--page-bg); }
  .sheet {
    position: absolute; left: 194px; top: 31px; width: 811px; height: 1050px;
    background: var(--white); overflow: hidden;
    box-shadow: 0 8px 24px rgba(0,0,0,.25);
  }
  .band-top {
    position: absolute; left: 0; top: 0; width: 100%; height: 83px;
    background: linear-gradient(120deg, #22398f 0%, #3557b0 40%, #2a47a0 70%, #23378c 100%);
  }
  .band-gray {
    position: absolute; left: 0; top: 83px; width: 100%; height: 121px;
    background: linear-gradient(110deg, #d0d0d2 0%, #eeeeef 45%, #dcdcde 75%, #e8e8ea 100%);
  }
  .website {
    position: absolute; left: 585px; top: 29px; display: flex; align-items: center; gap: 8px;
    font: 400 16px "Roboto Condensed", sans-serif; color: var(--white);
  }
  .headshot {
    position: absolute; left: 13px; top: 33px; width: 214px; height: 214px; border-radius: 50%;
    background: var(--white); padding: 6px;
  }
  .headshot-fill {
    width: 100%; height: 100%; border-radius: 50%;
    background: radial-gradient(circle at 50% 40%, #9a8a7e 0%, #6a6560 40%, #3a3b3e 100%);
  }
  .name {
    position: absolute; left: 270px; top: 109px;
    font: 700 35px "Arimo", sans-serif; color: var(--title-blue); white-space: nowrap;
  }
  .role {
    position: absolute; left: 272px; top: 146px;
    font: italic 33px "Tinos", serif; color: var(--ink); white-space: nowrap;
  }
  .summary {
    position: absolute; left: 29px; top: 276px; width: 200px;
    font: italic 16px/17.6px "Tinos", serif; color: var(--title-blue);
  }
  .main-fade {
    position: absolute; left: 220px; top: 860px; width: 591px; height: 124px;
    background: linear-gradient(160deg, rgba(255,255,255,0) 0%, #e2e2e4 45%, #ffffff 100%);
  }
  .experience { position: absolute; left: 270px; top: 274px; width: 496px; color: var(--ink); }
  .experience h2 {
    font: 400 23px/26px "Arimo", sans-serif; color: var(--title-blue); margin-bottom: 17px;
  }
  .experience p { font: 400 12.6px/14.8px "Arimo", sans-serif; }
  .experience h3 { font: 700 12.6px/14.8px "Arimo", sans-serif; margin: 14px 0 8px; }
  .experience ul { list-style: none; }
  .experience li {
    position: relative; padding-left: 23px; margin-bottom: 8px;
    font: 400 12.6px/14.8px "Arimo", sans-serif;
  }
  .experience li::before {
    content: ""; position: absolute; left: 2px; top: 4px; width: 7px; height: 7px;
    border-radius: 50%; background: var(--ink);
  }
  .brand-box {
    position: absolute; left: 29px; top: 847px; width: 163px; height: 121px;
    border: 1.5px solid #8a8a8c; display: flex; align-items: center; justify-content: center; gap: 8px;
  }
  .brand-mark { width: 12px; height: 12px; background: var(--core-blue); }
  .brand-name { font: 700 40px "Arimo", sans-serif; color: var(--core-blue); letter-spacing: 3px; }
  .footer-gray {
    position: absolute; left: 0; top: 984px; width: 220px; height: 44px;
    background: #bebec0; border-top: 1px solid #9c9c9e;
  }
  .footer-blue {
    position: absolute; left: 220px; top: 984px; width: 591px; height: 44px;
    background: var(--core-blue);
  }
  .footer-fade {
    position: absolute; left: 220px; top: 1028px; width: 591px; height: 22px;
    background: linear-gradient(90deg, #c8c8ca, #f2f2f3);
  }
  .contact {
    position: absolute; top: 995px; display: flex; align-items: center; gap: 9px;
    font: 400 17px "Roboto Condensed", sans-serif; color: var(--white);
  }
  .contact.phone { left: 305px; }
  .contact.email { left: 566px; }
</style>
</head>
<body>
  <main class="sheet">
    <div class="band-top"></div>
    <div class="band-gray"></div>

    <div class="website">
      <svg width="20" height="20" viewBox="0 0 20 20" fill="none" stroke="#fff" stroke-width="1.3">
        <circle cx="10" cy="10" r="8.5"/><ellipse cx="10" cy="10" rx="3.8" ry="8.5"/>
        <line x1="1.5" y1="10" x2="18.5" y2="10"/><path d="M3 5.5h14M3 14.5h14"/>
      </svg>
      <span>www.yourdomain.com</span>
    </div>

    <div class="headshot">
      <div class="headshot-fill" role="img" aria-label="Head shot portrait"></div>
    </div>

    <h1 class="name">Daniel Morrow Textboxname</h1>
    <p class="role">Marketing Executive</p>

    <p class="summary">Lorem ipsum dolor sit aamet, consectetur adipiscing eaalit. Quisque varius, mi sedabboa sedcondim entum graaaavida, ligula nunc maximus orci, sit amet mollis odio turpaaais et maris. Crasddd tempor mattis dictum. Vivaus interdum diam inlor emkkajjik mollis, atakjis tincdunt nullaaktab varius.aik Aliquam ut congquam. Seded pretium fringillabibendumaa cursus. Sed id ligula necasasa magna lacinia laoreet. Etiam id tempor velit. Phasellus sed dolor tincidunt, elementusam diam gravida, pharetra eros. Aenean diam dolor, laoreet ut lectus eu, eleife</p>

    <div class="main-fade"></div>

    <section class="experience">
      <h2>PROFESSIONAL<br>EXPERIENCES</h2>
      <p>Lorem ipsum dolor sit amet, consectetur adipiscing elit. Quisque varius, mi sed condimentum gravida, ligula nunc maximus orci, sit amet mollis odio turpis et mauris. Cras tempor mattis dictum. Vivamus interdum diam in lorem mollis, at tincidunt nulla varius. Aliquam ut congue quam. Sed pretium fringilla orci bibendum cursus. Sed id ligula nec magna lacinia laoreet. Etiam id tempor velit. Phasellus sed dolor tincidunt, elementum diam gravida, pharetra eros. Aenean diam dolor, laoreet ut lectus eu, eleifend varius urna. Etiam dictum ipsum quis hendrerit iaculis. Sed ut semper quam, sed consequat tortor. Curabitur ornare mollis eleifend. Quisque sem sem, efficitur luctus eros a, semper consequat arcu. Proin vel posuere quam, ut ultrices libero.</p>
      <h3>Lorem ipsum dolor sit amet, consectetur</h3>
      <ul>
        <li>Phasellus facilisis, nibh sed vestibulum semper, arcu turpis pellentesque est, eu mollis sem elit ac diam.</li>
        <li>In dictum velit eget nisl finibus euismod. Mauris aliquet finibus felis, ac vehicula quam maximus vitae. Maecenas ac dui eget elit tempor blandit auctor a lectus. Curabitur quis libero eu sem pretium placerat.</li>
        <li>Quisque maximus ligula velit, sit amet varius nisl interdum vel. Duis a ullamcorper massa, a pulvinar ante. Vivamus finibus odio sed ligula eleifend ullamcorper. Vivamus a iaculis diam. Aenean luctus dui in nunc sodales scelerisque.</li>
        <li>Phasellus tellus sem, egestas at erat quis, tincidunt fringilla nisi. Cras ultricies volutpat tortor.</li>
      </ul>
      <h3>Lorem ipsum dolor sit amet, consectetur</h3>
      <ul>
        <li>Phasellus facilisis, nibh sed vestibulum semper, arcu turpis pellentesque est, eu mollis sem elit ac diam.</li>
        <li>In dictum velit eget nisl finibus euismod. Mauris aliquet finibus felis, ac vehicula quam maximus vitae. Maecenas ac dui eget elit tempor blandit auctor a lectus. Curabitur quis libero eu sem pretium placerat.</li>
        <li>Quisque maximus ligula velit, sit amet varius nisl interdum vel. Duis a ullamcorper massa, a pulvinar ante. Vivamus finibus odio sed ligula eleifend ullamcorper. Vivamus a iaculis diam. Aenean luctus dui in nunc sodales scelerisque.</li>
        <li>Phasellus tellus sem, egestas at erat quis, tincidunt fringilla nisi. Cras ultricies volutpat tortor.</li>
      </ul>
    </section>

    <div class="brand-box">
      <span class="brand-mark"></span>
      <span class="brand-name">KVT</span>
    </div>

    <div class="footer-gray"></div>
    <div class="footer-blue"></div>
    <div class="footer-fade"></div>

    <div class="contact phone">
      <svg width="22" height="22" viewBox="0 0 22 22">
        <circle cx="11" cy="11" r="11" fill="#fff"/>
        <path d="M7.2 5.5c.6-.4 1.3-.2 1.6.4l1 2c.3.5.1 1.1-.3 1.4l-.8.6c.6 1.4 1.8 2.6 3.2 3.2l.6-.8c.3-.4.9-.6 1.4-.3l2 1c.6.3.8 1 .4 1.6l-.7 1c-.5.7-1.4 1-2.2.7-3.2-1.1-5.6-3.5-6.7-6.7-.3-.8 0-1.7.7-2.2z" fill="#263a80"/>
      </svg>
      <span>0098-7654-3210</span>
    </div>

    <div class="contact email">
      <svg width="20" height="20" viewBox="0 0 20 20" fill="none" stroke="#fff" stroke-width="1.4">
        <circle cx="10" cy="10" r="9"/>
        <rect x="5" y="6.5" width="10" height="7" rx="0.8"/>
        <path d="M5 7l5 4 5-4"/>
      </svg>
      <span>support@yourdomain.com</span>
    </div>
  </main>
</body>
</html>
```